Local Flower Farm Needs Business Card Design

I need business cards designed for a flower farm based in Eudora, Kansas.
Business Info:
We are a local cut flower farm located in Eudora, Kansas, founded by Corinne Haldwick. What started as a passion for agriculture and search for more joy in daily life has blossomed into a small business dedicated to providing the community with beautiful, fresh, and sustainable flowers. We specialize in local, seasonal blooms, ensuring that every petal reflects the care and dedication we pour into our craft. Our mission is to deliver the highest quality flowers directly to our customers through local farmers markets and to florists who share our commitment to sustainability. Join us in celebrating the beauty of nature, one bloom at a time!
Contact Details:
Corinne Haldwick
Owner
Phone 913-555-0147
Facebook: Rosalind Thorpe Gardens
Instagram: @RosalindThorpeGardens
Website: RosalindThorpeGardens.example
Target Market(s)
Wholesale to Florists and Direct to Consumer via Farmers Market
Industry/Entity Type
Florist, Farm
Contact Information for Business Card
Name, Contact Info, Logo
Look and feel
Each slider illustrates characteristics of the customer's brand and the style your logo design should communicate.

```html
<!DOCTYPE html>
<html lang="en">
<head>
<meta charset="utf-8">
<title>Rosalind Thorpe Gardens – Business Card</title>
<link rel="stylesheet" href="https://fonts.googleapis.com/css2?family=Montserrat:wght@300;400;500;700&display=swap">
<style>
  :root {
    --teal-deep: #0b282c;
    --teal-mid: #1d5a66;
    --sky: #55c6e2;
    --paper: #ffffff;
    --backdrop: #e9e8ea;
    --ink: #111b1d;
  }
  * { box-sizing: border-box; margin: 0; padding: 0; }
  html, body {
    width: 1200px; height: 1108px; overflow: hidden;
    background: var(--backdrop);
    font-family: "Montserrat", sans-serif;
  }
  .card {
    position: absolute; left: 219px; width: 775px; height: 473px;
    overflow: hidden;
  }
  .card-front { top: 50px; background: var(--paper); }
  .card-back { top: 568px; height: 457px; background: var(--teal-deep); }

  .name-band {
    position: absolute; left: 0; top: 40px; width: 100%; height: 85px;
    background: var(--teal-deep);
  }
  .brand-badge {
    position: absolute; left: 80px; top: 20px; width: 124px; height: 124px;
    border-radius: 50%; background: var(--paper);
    border: 2px solid var(--teal-deep);
    display: flex; align-items: center; justify-content: center;
    text-align: center; padding: 14px;
    font-size: 13px; font-weight: 700; line-height: 1.25;
    color: var(--teal-deep); text-transform: uppercase; letter-spacing: 0.5px;
  }
  .owner {
    position: absolute; right: 50px; top: 52px; text-align: right; color: var(--paper);
  }
  .owner-name { font-size: 29px; font-weight: 700; letter-spacing: 0.3px; line-height: 1.1; }
  .owner-role { font-size: 18px; font-weight: 300; margin-top: 2px; }

  .contact-list {
    position: absolute; left: 40px; top: 335px; list-style: none;
    color: var(--ink); font-size: 18px; font-weight: 400;
  }
  .contact-list li { display: flex; align-items: center; height: 28.7px; }
  .contact-icon { width: 17px; height: 17px; margin-right: 9px; flex: none; }

  .brand-feature {
    position: absolute; right: 54px; top: 230px; text-align: right;
    font-size: 40px; font-weight: 700; line-height: 1.15; color: var(--teal-deep);
  }

  .monogram-pattern {
    position: absolute; inset: 0;
    background: linear-gradient(125deg, var(--sky) 0%, var(--teal-mid) 32%, var(--teal-deep) 62%);
  }
  .back-brand {
    position: absolute; left: 520px; top: 290px; width: 100px;
    text-align: center; color: var(--paper);
    font-size: 15px; font-weight: 700; line-height: 1.2; text-transform: uppercase;
  }
</style>
</head>
<body>
  <section class="card card-front">
    <div class="name-band"></div>
    <div class="brand-badge">Rosalind Thorpe Gardens</div>
    <div class="owner">
      <p class="owner-name">Corinne Haldwick</p>
      <p class="owner-role">Owner</p>
    </div>
    <ul class="contact-list">
      <li>
        <svg class="contact-icon" viewBox="0 0 24 24" aria-hidden="true"><path fill="var(--ink)" d="M6.6 10.8a15 15 0 0 0 6.6 6.6l2.2-2.2c.3-.3.7-.4 1-.2 1.1.4 2.3.6 3.6.6.6 0 1 .4 1 1V20c0 .6-.4 1-1 1A17 17 0 0 1 3 4c0-.6.4-1 1-1h3.5c.6 0 1 .4 1 1 0 1.3.2 2.5.6 3.6.1.3 0 .7-.2 1z"/></svg>
        913-555-0147
      </li>
      <li>
        <svg class="contact-icon" viewBox="0 0 24 24" aria-hidden="true"><circle cx="12" cy="12" r="10" fill="var(--ink)"/></svg>
        Rosalind Thorpe Gardens
      </li>
      <li>
        <svg class="contact-icon" viewBox="0 0 24 24" aria-hidden="true"><circle cx="12" cy="12" r="10" fill="var(--ink)"/></svg>
        @RosalindThorpeGardens
      </li>
      <li>
        <svg class="contact-icon" viewBox="0 0 24 24" aria-hidden="true"><circle cx="12" cy="12" r="10" fill="none" stroke="var(--ink)" stroke-width="2.4"/><path d="M2 12h20M12 2c3 3 3 17 0 20M12 2c-3 3-3 17 0 20" fill="none" stroke="var(--ink)" stroke-width="1.8"/></svg>
        www.RosalindThorpeGardens.example
      </li>
    </ul>
    <div class="brand-feature">Rosalind<br>Thorpe<br>Gardens</div>
  </section>

  <section class="card card-back">
    <div class="monogram-pattern" role="img" aria-label="Repeating floral monogram pattern fading from light blue at the top left into dark teal"></div>
    <div class="back-brand">Rosalind Thorpe Gardens</div>
  </section>
</body>
</html>
```